Brisk Rainshield - Logo and Advert

Help to provide logo and advert.
Advert is to be short and concise to fit in a printed directory posted around homes.
Ideally the same advert to be able to be blown up as a leaflet.
Use of eco friendly type colours, soft greens and blues.
Logo to be subtle but indicative to roofing and facades.
Breakdown of advert as follows;
Company name:
Brisk Rainshield
Sub title:
Roofing & Façades
Services breakdown:
Pitched (Slating & Tiling)
Flat (Single Ply, Liquid & Mineral Felt)
Hard Metal (Zinc Standing Seam)
Leadwork
Roof lights and lanterns
Generic notes:
100% flame free applications available, eliminating all fire risks to your property. (No gas torch’s etc.).
Expert consultation and advice.
Product warranty and/or insurance backed warranty available.
Fully insured contractor.
Contact information:
Phone number to be confirmed
Email and/or website to be confirmed.
Please feel free to try out different colours and fonts other than outlined. I am not limited to those and open to suggestions.
Target Market(s)
Domestic/Private Home Owners/Small Buidlers
Industry/Entity Type
Roofing
Font styles to use
Look and feel
Each slider illustrates characteristics of the customer's brand and the style your logo design should communicate.

```html
<!DOCTYPE html>
<html lang="en">
<head>
<meta charset="utf-8">
<title>Brisk Rainshield – Roofing and Facades</title>
<link rel="stylesheet" href="https://fonts.googleapis.com/css2?family=Bebas+Neue&family=Barlow:wght@400;500;700&family=Barlow+Condensed:wght@600;700&display=swap">
<style>
  :root {
    --sky-blue: #29a3d8;
    --deep-blue: #2a7fcf;
    --footer-blue: #2462c6;
    --navy: #1f3352;
    --warranty-navy: #1e5a86;
    --alert-red: #fb2222;
    --white: #ffffff;
    --ink: #1b1b1b;
  }
  * { margin: 0; padding: 0; box-sizing: border-box; }
  html, body { width: 927px; height: 1200px; overflow: hidden; background: var(--white); }
  .flyer { position: relative; width: 927px; height: 1200px; overflow: hidden; font-family: "Barlow", sans-serif; color: var(--white); }
  .backdrop { position: absolute; inset: 0; }
  .brand { position: absolute; left: 52px; top: 90px; width: 314px; text-align: center; color: var(--ink); }
  .brand-mark { display: inline-block; width: 14px; height: 14px; background: var(--sky-blue); margin-bottom: 8px; }
  .brand-name { font-family: "Barlow", sans-serif; font-weight: 700; font-size: 19px; letter-spacing: 0.5px; }
  .brand-tagline { font-size: 7.5px; letter-spacing: 4.6px; margin-top: 2px; }
  .headline { position: absolute; left: 94px; top: 178px; font-family: "Bebas Neue", sans-serif; font-size: 82px; line-height: 64px; color: var(--sky-blue); }
  .insured-pill { position: absolute; left: 631px; top: 52px; width: 296px; height: 67px; background: var(--alert-red); border-radius: 34px 0 0 34px; display: flex; align-items: center; padding-left: 26px; font-family: "Barlow Condensed", sans-serif; font-weight: 700; font-size: 25px; }
  .services-title { position: absolute; left: 53px; top: 572px; font-family: "Bebas Neue", sans-serif; font-size: 56px; line-height: 1; }
  .services-list { position: absolute; left: 55px; top: 633px; list-style: none; font-size: 26px; line-height: 33px; }
  .services-list li { display: flex; align-items: center; }
  .services-list svg { width: 20px; height: 20px; margin-right: 16px; }
  .flame-note { position: absolute; left: 91px; top: 836px; font-size: 26px; line-height: 33.5px; }
  .consult-pill { position: absolute; left: 548px; top: 910px; width: 379px; height: 89px; background: var(--deep-blue); border-radius: 45px 0 0 45px; padding: 15px 0 0 45px; font-weight: 700; font-size: 25px; line-height: 31px; }
  .warranty { position: absolute; left: 0; top: 1050px; width: 927px; text-align: center; font-family: "Barlow Condensed", sans-serif; font-weight: 700; font-size: 31px; color: var(--warranty-navy); }
  .call { position: absolute; left: 47px; top: 1116px; font-family: "Bebas Neue", sans-serif; font-size: 66px; line-height: 1; }
  .contact { position: absolute; left: 572px; top: 1131px; list-style: none; font-family: "Barlow Condensed", sans-serif; font-weight: 600; font-size: 18px; letter-spacing: 2px; line-height: 26px; }
  .contact li { display: flex; align-items: center; }
  .contact svg { width: 18px; height: 18px; margin-right: 15px; }
</style>
</head>
<body>
<div class="flyer">
  <svg class="backdrop" width="927" height="1200" viewBox="0 0 927 1200">
    <defs>
      <linearGradient id="roofTones" x1="0" y1="0" x2="1" y2="1">
        <stop offset="0" stop-color="#8d9297"/>
        <stop offset="0.45" stop-color="#6f777e"/>
        <stop offset="0.7" stop-color="#5d6a5a"/>
        <stop offset="1" stop-color="#7b8088"/>
      </linearGradient>
      <linearGradient id="lanternTones" x1="0" y1="0" x2="0" y2="1">
        <stop offset="0" stop-color="#4f8a5a"/><stop offset="0.5" stop-color="#3a4a5c"/><stop offset="1" stop-color="#8a8f95"/>
      </linearGradient>
      <linearGradient id="membraneTones" x1="0" y1="0" x2="1" y2="0">
        <stop offset="0" stop-color="#d8dde2"/><stop offset="0.35" stop-color="#7fb0d8"/><stop offset="1" stop-color="#3d86c4"/>
      </linearGradient>
      <linearGradient id="claddingTones" x1="0" y1="0" x2="1" y2="1">
        <stop offset="0" stop-color="#6e7379"/><stop offset="1" stop-color="#9a9ea3"/>
      </linearGradient>
      <linearGradient id="edgeTones" x1="0" y1="0" x2="1" y2="1">
        <stop offset="0" stop-color="#5a5e63"/><stop offset="0.6" stop-color="#2f3237"/><stop offset="1" stop-color="#b9bcbf"/>
      </linearGradient>
    </defs>
    <polygon points="0,0 927,0 927,406 0,520" fill="url(#roofTones)" role="img" aria-label="Photo of a grey tiled pitched roof with trees behind"/>
    <polygon points="0,552 927,434 927,1035 0,1035" fill="var(--sky-blue)"/>
    <path d="M0,809 H430 A95,95 0 0 1 430,999 H0 Z" fill="var(--deep-blue)"/>
    <polygon points="52,0 366,0 366,393 52,431" fill="var(--white)"/>
    <polygon points="52,431 366,393 366,402 52,449" fill="var(--sky-blue)"/>
    <g class="photo-frames">
      <polygon points="592,187 877,148 877,299 592,336" fill="var(--white)"/>
      <polygon points="599,194 870,157 870,292 599,328" fill="url(#lanternTones)" role="img" aria-label="Photo of a glass roof lantern on a flat roof"/>
      <polygon points="592,367 877,328 877,479 592,516" fill="var(--white)"/>
      <polygon points="599,374 870,337 870,472 599,508" fill="url(#membraneTones)" role="img" aria-label="Photo of a rolled waterproof membrane with water droplets"/>
      <polygon points="592,545 877,506 877,657 592,694" fill="var(--white)"/>
      <polygon points="599,552 870,515 870,650 599,686" fill="url(#claddingTones)" role="img" aria-label="Photo of grey standing seam metal cladding"/>
      <polygon points="592,725 877,686 877,837 592,874" fill="var(--white)"/>
      <polygon points="599,732 870,695 870,830 599,866" fill="url(#edgeTones)" role="img" aria-label="Photo of a dark single ply membrane roof edge"/>
    </g>
    <rect x="0" y="1098" width="927" height="102" fill="var(--footer-blue)"/>
    <polygon points="541,1116 927,1116 927,1200 526,1200" fill="var(--navy)"/>
  </svg>

  <div class="brand">
    <span class="brand-mark"></span>
    <div class="brand-name">BRISK RAINSHIELD</div>
    <div class="brand-tagline">ROOFING AND FACADES</div>
  </div>

  <h1 class="headline">ROOFING<br>AND<br>FACADES</h1>

  <div class="insured-pill">FULLY INSURED CONTRACTOR</div>

  <h2 class="services-title">SERVICES</h2>
  <ul class="services-list">
    <li><svg viewBox="0 0 20 20"><path d="M2 11 L8 17 L18 3" fill="none" stroke="#fff" stroke-width="3"/></svg>Pitched (Slating &amp; Tiling)</li>
    <li><svg viewBox="0 0 20 20"><path d="M2 11 L8 17 L18 3" fill="none" stroke="#fff" stroke-width="3"/></svg>Flat (Single Ply, Liquid &amp; Mineral Felt)</li>
    <li><svg viewBox="0 0 20 20"><path d="M2 11 L8 17 L18 3" fill="none" stroke="#fff" stroke-width="3"/></svg>Hard Metal (Zinc Standing Seam)</li>
    <li><svg viewBox="0 0 20 20"><path d="M2 11 L8 17 L18 3" fill="none" stroke="#fff" stroke-width="3"/></svg>Leadwork</li>
    <li><svg viewBox="0 0 20 20"><path d="M2 11 L8 17 L18 3" fill="none" stroke="#fff" stroke-width="3"/></svg>Roof lights and lanterns</li>
  </ul>

  <p class="flame-note">100% flame free applications<br>available, eliminating all fire<br>risks to your property.<br>(No gas torch’s etc.)</p>

  <div class="consult-pill">EXPERT CONSULTATION<br>AND ADVICE</div>

  <p class="warranty">PRODUCT WARRANTY AND/OR ISSURANCE BACKED WARRANTY AVAILABLE</p>

  <p class="call">CALL 1800 555 019</p>

  <ul class="contact">
    <li><svg viewBox="0 0 20 20" fill="none" stroke="#fff" stroke-width="1.5"><circle cx="10" cy="10" r="8"/><ellipse cx="10" cy="10" rx="3.5" ry="8"/><path d="M2 10 H18 M3.5 6 H16.5 M3.5 14 H16.5"/></svg>WWW.BRISKRAINSHIELD.COM</li>
    <li><svg viewBox="0 0 20 20" fill="none" stroke="#fff" stroke-width="1.5"><rect x="2" y="4" width="16" height="12"/><path d="M2 4 L10 11 L18 4 M2 16 L8 10 M18 16 L12 10"/></svg>HELLO@BRISKRAINSHIELD.COM</li>
  </ul>
</div>
</body>
</html>
```